New Company Business Card design

Looking for a corporate looking business card utilising my new logo design - the logo i would like embossed as one option and flat as another - simplistic but stylish - less is more - we are an import export business launching into the market - i would like a couple of options as main background - Grey or Black

```html
<!DOCTYPE html>
<html lang="en">
<head>
<meta charset="utf-8">
<title>Meridian Trade Partners – Business Card</title>
<link href="https://fonts.googleapis.com/css2?family=Roboto:wght@400;500&display=swap" rel="stylesheet">
<style>
  :root {
    --backdrop: #ad8862;
    --card-black: #1b1b1d;
    --card-blue: #1076bf;
    --arc-grey: #6b6b6e;
    --ink-white: #ffffff;
    --ink-soft: #e6eef6;
  }
  * { margin: 0; padding: 0; box-sizing: border-box; }
  html, body { width: 1200px; height: 960px; overflow: hidden; }
  body {
    background: var(--backdrop);
    font-family: "Roboto", Arial, sans-serif;
    position: relative;
  }
  .card {
    position: absolute;
    width: 600px;
    height: 342px;
    background: var(--card-black);
    box-shadow: 0 3px 8px rgba(0,0,0,0.35);
    overflow: hidden;
  }
  .card--front { left: 314px; top: 113px; }
  .card--back  { left: 311px; top: 472px; }

  .front-shapes { position: absolute; inset: 0; }

  .front-mark {
    position: absolute;
    left: 84px;
    top: 120px;
    width: 230px;
    text-align: center;
    font-size: 92px;
    font-weight: 500;
    color: var(--ink-white);
    line-height: 1;
  }

  .contact {
    position: absolute;
    left: 356px;
    top: 76px;
    color: var(--ink-white);
  }
  .contact__name { font-size: 22px; font-weight: 500; letter-spacing: 0.2px; line-height: 1.1; }
  .contact__role { font-size: 15px; font-weight: 400; margin-top: 2px; }
  .contact__address { font-size: 14.5px; line-height: 19px; margin-top: 6px; color: var(--ink-soft); }
  .contact__list { list-style: none; margin-top: 7px; }
  .contact__list li {
    display: flex; align-items: center;
    font-size: 14.5px; line-height: 19.2px; color: var(--ink-soft);
  }
  .contact__icon { width: 12px; height: 12px; margin-right: 10px; fill: var(--ink-white); flex: none; }

  .back-brand {
    position: absolute;
    left: 0; right: 0; top: 194px;
    text-align: center;
    color: var(--ink-white);
  }
  .back-brand__name {
    display: inline-flex; align-items: center; gap: 10px;
    font-size: 20px; font-weight: 500; letter-spacing: 0.8px; line-height: 24px;
  }
  .back-brand__dot { width: 12px; height: 12px; border-radius: 50%; background: var(--ink-white); }
  .back-brand__tagline {
    margin-top: 10px;
    font-size: 9.5px; letter-spacing: 2.6px; text-transform: uppercase;
  }
  .back-web {
    position: absolute;
    left: 0; right: 0; top: 288px;
    text-align: center;
    font-size: 14px; letter-spacing: 2.2px;
    color: var(--ink-white);
  }
</style>
</head>
<body>

<section class="card card--front">
  <svg class="front-shapes" width="600" height="342" viewBox="0 0 600 342" aria-hidden="true">
    <circle cx="176" cy="171" r="175" fill="var(--arc-grey)"/>
    <rect x="176" y="0" width="424" height="342" fill="var(--arc-grey)"/>
    <circle cx="212" cy="171" r="174" fill="var(--card-blue)"/>
    <rect x="212" y="0" width="388" height="342" fill="var(--card-blue)"/>
  </svg>

  <div class="front-mark">MTP</div>

  <div class="contact">
    <p class="contact__name">DANIEL HART</p>
    <p class="contact__role">CEO/FOUNDER</p>
    <p class="contact__address">2140 Harbor View Road<br>Seaport, Oregon 97120</p>
    <ul class="contact__list">
      <li><svg class="contact__icon" viewBox="0 0 12 12"><path d="M2.5 0.8l2 2.2-1 1.5c.7 1.5 1.8 2.6 3.3 3.3l1.5-1 2.2 2-1.2 2.1C4.8 10.6 1.4 7.2.6 2z"/></svg>503 218 4470</li>
      <li><svg class="contact__icon" viewBox="0 0 12 12"><path d="M3 0h6v12H3zM4 1.5v8h4v-8zM5.5 10.3h1v.9h-1z" fill-rule="evenodd"/></svg>503 774 1926</li>
      <li><svg class="contact__icon" viewBox="0 0 12 12"><path d="M3 0h6v3H3zM0 4h12v5h-2v3H2V9H0zM3 7v4h6V7z" fill-rule="evenodd"/></svg>503 218 4471</li>
      <li><svg class="contact__icon" viewBox="0 0 12 12"><path d="M0 2h12v8H0zM1 3l5 3.5L11 3v-.1H1z" fill-rule="evenodd"/></svg>daniel@meridiantp.com</li>
      <li><svg class="contact__icon" viewBox="0 0 12 12"><circle cx="6" cy="6" r="6"/><path d="M2 4.5c1.5 0 2 1.5 3 1.5s.5 2 1.5 3.5M7 1.5c0 1.5 2 1.5 2.5 3" stroke="var(--card-blue)" stroke-width="1.2" fill="none"/></svg>www.meridiantp.com</li>
    </ul>
  </div>
</section>

<section class="card card--back">
  <div class="back-brand">
    <p class="back-brand__name"><span class="back-brand__dot"></span>MERIDIAN TRADE PARTNERS</p>
    <p class="back-brand__tagline">Trusted trade across every border</p>
  </div>
  <p class="back-web">www.meridiantradepartners.com</p>
</section>

</body>
</html>
```